Lark Vista Perks Needs a Website Design

We need a website design for a new service we are starting. Users enter a coupon in a redemption page and either create an account or sign in. they can then use the credits they accumulate from the coupons to purchase items listed on the site.

we need a design for the following:
-the coupon redemption page (with a choice to either sign in or create an account)
-a product listing page (with search filters and a search bar. the search bar can be displayed in the header of the site)
-a product detail page, showing the product's title, image, credit redemption value, brand and any category associated with the item
-a my account page, with:
*a list of the pluses (coupons/credit added to account) and the minuses (orders placed/credits subtracted from account) to show a detailed description of their history on the site)
*an area for users to edit their name, phone number, address etc
*an area for users to add / edit their casino membership number and casino
*an area for users to add a coupon to their account
-a cart / checkout process:
*cart displaying items and their total
*entering / selecting an address from their account
*review order details page where they can submit their order (and warning the user that doing so will subtract the required credits from their account)

remember that no ecommerce or money is used on the site.. users are spending their credits and checkout their cart with the credits they accumulated, so the items each have a credit redemption value and the checkout process is shown in credits.

we are not very particular with any design preference, other than we'd like it to be predominately white.

If designing the site with css please make sure to use bootstrap in your designs. thanks!

Target Market(s)

adults 45-65

Industry/Entity Type

Casino

Coding

Coded - Design and coding required

Number of Pages Required

5+ page

Font styles to use
Sans Serif

Requirements
Must have
• css must use with bootstrap
Nice to have
• simplified, easy interface. we are targeting an older crowd and dont want to confuse them
Should not have
• the site shouldnt have any dollar values. all product prices, checkout totals and user accrual's (in the my account page) should be in credits

```html
<!DOCTYPE html>
<html lang="en">
<head>
<meta charset="utf-8">
<title>Lark Vista Perks</title>
<link href="https://fonts.googleapis.com/css2?family=Open+Sans:wght@400;600;700&family=Roboto+Condensed:wght@400;700&display=swap" rel="stylesheet">
<style>
:root{
  --brand:#1f5a9e;
  --accent:#2fa4d8;
  --green:#3d8b2f;
  --btn-green:#5dbb2c;
  --navy:#27336f;
  --text:#333;
  --muted:#777;
  --icon:#8a8a8a;
  --line:#e3e3e3;
  --soft:#f4f4f4;
}
*{box-sizing:border-box;margin:0;padding:0}
html,body{width:697px;height:1200px;overflow:hidden;background:#fff}
body{font-family:"Open Sans",sans-serif;color:var(--text);position:relative}
.abs{position:absolute}
.logo{left:57px;top:24px;font-size:22px;font-weight:600;color:var(--brand);display:flex;align-items:center;gap:6px}
.logo i{width:12px;height:12px;border-radius:50%;background:var(--brand);display:inline-block}
.search{left:335px;top:31px;width:191px;height:20px;border:1px solid #ddd;display:flex;font-size:7px;align-items:center}
.search .cat{width:57px;height:100%;background:var(--soft);border-right:1px solid #ddd;display:flex;align-items:center;justify-content:center;color:#555}
.search .q{flex:1;padding-left:12px;color:#555}
.search svg{margin-right:8px}
.user-links{left:533px;top:29px;display:flex;gap:20px;font-size:7px;color:#555;text-align:center}
.user-links div{display:flex;flex-direction:column;align-items:center;gap:5px}
.nav{left:0;top:77px;width:697px;height:28px;background:var(--brand);display:flex;padding-left:57px}
.nav a{color:#fff;font-size:7.5px;text-decoration:none;padding:0 15px;line-height:28px;border-right:1px solid rgba(255,255,255,.15)}
.hero{left:57px;top:117px;width:582px;height:243px;background:linear-gradient(100deg,#8a9098,#a3a9ad 45%,#7d8688)}
.hero-phones{left:380px;top:150px;width:165px;height:178px;background:linear-gradient(90deg,#222,#e8e8e8 30%,#f7a0c0 50%,#f3e86a 65%,#6fc3ee 80%,#8fdf5a);border-radius:10px}
.hero-title{left:134px;top:176px;font-family:"Roboto Condensed",sans-serif;font-weight:700;color:#fff;font-size:29px;line-height:29px}
.hero-text{left:134px;top:238px;color:#fff;font-size:8px;line-height:13px;width:160px}
.hero-btn{left:134px;top:273px;background:var(--accent);color:#fff;font-size:8.5px;padding:5px 10px}
.arrow{width:20px;height:20px;border-radius:50%;background:#333;display:flex;align-items:center;justify-content:center}
.promo{top:370px;width:188px;height:121px;border-bottom:2px solid #8bc34a}
.promo .t{position:absolute;right:10px;top:40px;font-family:"Roboto Condensed",sans-serif;font-weight:700;font-size:12px;line-height:15px;text-align:right;color:#222}
.promo .b{position:absolute;right:13px;top:80px;background:var(--btn-green);color:#fff;font-size:6px;padding:5px 10px;border-radius:10px}
.section-title{left:57px;top:524px;font-family:"Roboto Condensed",sans-serif;font-size:15px;font-weight:400;color:#222}
.pager{left:610px;top:525px;display:flex;gap:4px}
.pager span{width:13px;height:13px;border:1px solid #777;border-radius:50%}
.card{width:134px;height:184px;border:1px solid var(--line)}
.card .img{position:absolute;left:20px;top:8px;width:92px;height:92px;border-radius:4px}
.card .name{position:absolute;top:106px;width:100%;text-align:center;font-size:7.5px;line-height:11px;color:#444}
.card .price{position:absolute;top:131px;width:100%;text-align:center;font-size:12px;font-weight:700;color:var(--green)}
.card .acts{position:absolute;bottom:0;left:0;right:0;height:28px;background:var(--soft);border-top:1px solid var(--line);display:flex}
.card .acts span{flex:1;border-right:1px solid var(--line);display:flex;align-items:center;justify-content:center}
.card .acts span:last-child{border:none}
.footer{left:0;top:1006px;width:697px;height:162px;background:#f6f6f6}
.fh{font-family:"Roboto Condensed",sans-serif;font-size:12px;font-weight:400;color:#333}
.counter{display:flex;gap:2px}
.counter span{width:16px;height:24px;border:1px solid #bbb;background:#fff;font-size:15px;display:flex;align-items:center;justify-content:center;border-radius:2px}
.social{display:flex;gap:4px}
.social span{width:10px;height:10px}
.contact{font-size:7.5px;color:#666;line-height:11px}
.links{font-size:6.5px;color:#666;line-height:12px}
.field{width:152px;height:24px;background:#fff;border:1px solid #e0e0e0;font-size:6.5px;color:#555;padding-left:8px;display:flex;align-items:center}
.signup{background:var(--navy);color:#fff;font-size:7px;font-weight:700;display:flex;align-items:center;justify-content:center}
.pay span{display:inline-block;width:22px;height:13px;border:1px solid #ccc;border-radius:2px;margin-right:3px;background:#fff}
.rule{left:0;top:1168px;width:697px;height:1px;background:var(--line)}
.copy{left:0;top:1180px;width:697px;text-align:center;font-size:6.5px;color:#555}
</style>
</head>
<body>
<svg width="0" height="0" style="position:absolute">
  <symbol id="i-cart" viewBox="0 0 10 9"><path d="M0 0.5h2l1.5 5h5l1-3.5H3" fill="none" stroke="currentColor" stroke-width="1.2"/><circle cx="4" cy="7.8" r="0.9" fill="currentColor"/><circle cx="8" cy="7.8" r="0.9" fill="currentColor"/></symbol>
  <symbol id="i-heart" viewBox="0 0 10 9"><path d="M5 9L1 5a2.4 2.4 0 0 1 4-3a2.4 2.4 0 0 1 4 3z" fill="currentColor"/></symbol>
  <symbol id="i-swap" viewBox="0 0 10 9"><path d="M0 3h8M6 1l2 2-2 2M10 6H2M4 4L2 6l2 2" fill="none" stroke="currentColor" stroke-width="1.1"/></symbol>
  <symbol id="i-eye" viewBox="0 0 10 9"><path d="M0.5 4.5Q5 -0.5 9.5 4.5Q5 9.5 0.5 4.5z" fill="none" stroke="currentColor" stroke-width="1"/><circle cx="5" cy="4.5" r="1.5" fill="currentColor"/></symbol>
</svg>

<header>
  <div class="abs logo"><i></i>Lark Vista Perks</div>
  <div class="abs search"><div class="cat">Categories ▾</div><div class="q">What are you looking for</div>
    <svg width="8" height="8" viewBox="0 0 10 10"><circle cx="4" cy="4" r="3" fill="none" stroke="#333" stroke-width="1.4"/><path d="M6.5 6.5L9 9" stroke="#333" stroke-width="1.4"/></svg></div>
  <div class="abs user-links">
    <div><svg width="9" height="10" viewBox="0 0 9 10"><rect x="1" y="4" width="7" height="6" fill="#777"/><path d="M2.5 4V2.5a2 2 0 0 1 4 0" fill="none" stroke="#777"/></svg>LOGIN</div>
    <div><svg width="10" height="10" viewBox="0 0 10 10"><circle cx="5" cy="3" r="2.5" fill="#777"/><path d="M0 10a5 4 0 0 1 10 0z" fill="#777"/></svg>REGISTER</div>
    <div><svg width="12" height="10" viewBox="0 0 12 10"><ellipse cx="5" cy="4" rx="5" ry="3.5" fill="#777"/><ellipse cx="8" cy="6" rx="4" ry="3" fill="#999"/></svg>FAQ</div>
  </div>
</header>
<nav class="abs nav"><a>HOME</a><a>ABOUT US</a><a>COUPON REDEMPTION</a><a>PRODUCT LISTING</a><a>FOR SALE</a><a>NEWS</a><a>CONTACT US</a></nav>

<section class="abs hero" role="img" aria-label="Blurred photo of a hand holding a phone"></section>
<div class="abs hero-phones" role="img" aria-label="Row of colourful smartphones"></div>
<h1 class="abs hero-title">COUPON<br>REDEMPTION</h1>
<p class="abs hero-text">Lorem ipsum dolor sit amet, consectetur adipiscing elit, tempor incididunt</p>
<div class="abs hero-btn">SHOP NOW ➜</div>
<div class="abs arrow" style="left:91px;top:227px"><svg width="6" height="8"><path d="M5 0L1 4l4 4" stroke="#fff" fill="none" stroke-width="1.5"/></svg></div>
<div class="abs arrow" style="left:593px;top:227px"><svg width="6" height="8"><path d="M1 0l4 4-4 4" stroke="#fff" fill="none" stroke-width="1.5"/></svg></div>

<div class="abs promo" style="left:57px;background:linear-gradient(90deg,#e6e6e6,#fafafa)" role="img" aria-label="Headphones photo"><span class="t">AUDIO PLAYER &amp;<br>MUSIC MP3</span><span class="b">SHOP NOW</span></div>
<div class="abs promo" style="left:254px;background:linear-gradient(90deg,#b89a74,#c9ab85)" role="img" aria-label="Power bank and phone on wood"><span class="t">SMARTPHONE<br>CHARGER</span><span class="b">SHOP NOW</span></div>
<div class="abs promo" style="left:451px;background:linear-gradient(90deg,#b8c4a0,#eeeeee)" role="img" aria-label="Stack of colourful phone cases"><span class="t">MOBILE<br>PHONE CASES</span><span class="b">SHOP NOW</span></div>

<h2 class="abs section-title">FEATURE PRODUCTS</h2>
<div class="abs pager"><span></span><span></span></div>

<div class="abs card" style="left:57px;top:562px"><div class="img" role="img" aria-label="Waste disposer" style="background:linear-gradient(#fff,#555 40%,#222)"></div><div class="name">SED UT PERSPICIATIS UNDE<br>OMNIS ISTE NATUS</div><div class="price">6,950 Credits</div><div class="acts"><span><svg width="10" height="9" color="#8a8a8a"><use href="#i-cart"/></svg></span><span><svg width="10" height="9" color="#8a8a8a"><use href="#i-heart"/></svg></span><span><svg width="10" height="9" color="#8a8a8a"><use href="#i-swap"/></svg></span><span><svg width="10" height="9" color="#8a8a8a"><use href="#i-eye"/></svg></span></div></div>
<div class="abs card" style="left:206px;top:562px"><div class="img" role="img" aria-label="Earphones with music player" style="background:linear-gradient(#fff,#d7eeee 60%,#3fb4b0)"></div><div class="name">SED UT PERSPICIATIS UNDE<br>OMNIS ISTE NATUS</div><div class="price">6,950 Credits</div><div class="acts"><span><svg width="10" height="9" color="#8a8a8a"><use href="#i-cart"/></svg></span><span><svg width="10" height="9" color="#8a8a8a"><use href="#i-heart"/></svg></span><span><svg width="10" height="9" color="#8a8a8a"><use href="#i-swap"/></svg></span><span><svg width="10" height="9" color="#8a8a8a"><use href="#i-eye"/></svg></span></div></div>
<div class="abs card" style="left:354px;top:562px"><div class="img" role="img" aria-label="Smartphone front and back" style="background:linear-gradient(90deg,#c9b9a0,#222 55%,#111)"></div><div class="name">SED UT PERSPICIATIS UNDE<br>OMNIS ISTE NATUS</div><div class="price">6,950 Credits</div><div class="acts"><span><svg width="10" height="9" color="#8a8a8a"><use href="#i-cart"/></svg></span><span><svg width="10" height="9" color="#8a8a8a"><use href="#i-heart"/></svg></span><span><svg width="10" height="9" color="#8a8a8a"><use href="#i-swap"/></svg></span><span><svg width="10" height="9" color="#8a8a8a"><use href="#i-eye"/></svg></span></div></div>
<div class="abs card" style="left:506px;top:562px"><div class="img" role="img" aria-label="Steam iron" style="background:linear-gradient(135deg,#fff,#6fb2d8 60%,#cfd4d8)"></div><div class="name">SED UT PERSPICIATIS UNDE<br>OMNIS ISTE NATUS</div><div class="price">6,950 Credits</div><div class="acts"><span><svg width="10" height="9" color="#8a8a8a"><use href="#i-cart"/></svg></span><span><svg width="10" height="9" color="#8a8a8a"><use href="#i-heart"/></svg></span><span><svg width="10" height="9" color="#8a8a8a"><use href="#i-swap"/></svg></span><span><svg width="10" height="9" color="#8a8a8a"><use href="#i-eye"/></svg></span></div></div>

<div class="abs card" style="left:57px;top:768px"><div class="img" role="img" aria-label="Microwave oven" style="background:linear-gradient(135deg,#eee,#9a9a9a 60%,#555)"></div><div class="name">SED UT PERSPICIATIS UNDE<br>OMNIS ISTE NATUS</div><div class="price">6,950 Credits</div><div class="acts"><span><svg width="10" height="9" color="#8a8a8a"><use href="#i-cart"/></svg></span><span><svg width="10" height="9" color="#8a8a8a"><use href="#i-heart"/></svg></span><span><svg width="10" height="9" color="#8a8a8a"><use href="#i-swap"/></svg></span><span><svg width="10" height="9" color="#8a8a8a"><use href="#i-eye"/></svg></span></div></div>
<div class="abs card" style="left:206px;top:768px"><div class="img" role="img" aria-label="Blue and green headphones" style="background:radial-gradient(#3a8fd0,#cfe86a 50%,#fff 75%)"></div><div class="name">SED UT PERSPICIATIS UNDE<br>OMNIS ISTE NATUS</div><div class="price">6,950 Credits</div><div class="acts"><span><svg width="10" height="9" color="#8a8a8a"><use href="#i-cart"/></svg></span><span><svg width="10" height="9" color="#8a8a8a"><use href="#i-heart"/></svg></span><span><svg width="10" height="9" color="#8a8a8a"><use href="#i-swap"/></svg></span><span><svg width="10" height="9" color="#8a8a8a"><use href="#i-eye"/></svg></span></div></div>
<div class="abs card" style="left:354px;top:768px"><div class="img" role="img" aria-label="Cream jars with leaves" style="background:linear-gradient(#fff,#a7b27a 60%,#556b2f)"></div><div class="name">SED UT PERSPICIATIS UNDE<br>OMNIS ISTE NATUS</div><div class="price">6,950 Credits</div><div class="acts"><span><svg width="10" height="9" color="#8a8a8a"><use href="#i-cart"/></svg></span><span><svg width="10" height="9" color="#8a8a8a"><use href="#i-heart"/></svg></span><span><svg width="10" height="9" color="#8a8a8a"><use href="#i-swap"/></svg></span><span><svg width="10" height="9" color="#8a8a8a"><use href="#i-eye"/></svg></span></div></div>
<div class="abs card" style="left:506px;top:768px"><div class="img" role="img" aria-label="Headphones with phone" style="background:linear-gradient(135deg,#fff,#444 55%,#222)"></div><div class="name">SED UT PERSPICIATIS UNDE<br>OMNIS ISTE NATUS</div><div class="price">6,950 Credits</div><div class="acts"><span><svg width="10" height="9" color="#8a8a8a"><use href="#i-cart"/></svg></span><span><svg width="10" height="9" color="#8a8a8a"><use href="#i-heart"/></svg></span><span><svg width="10" height="9" color="#8a8a8a"><use href="#i-swap"/></svg></span><span><svg width="10" height="9" color="#8a8a8a"><use href="#i-eye"/></svg></span></div></div>

<footer class="abs footer">
  <h3 class="abs fh" style="left:58px;top:21px">VISITORS COUNT</h3>
  <div class="abs counter" style="left:58px;top:51px"><span>0</span><span>0</span><span>3</span><span>1</span><span>4</span><span>6</span></div>
  <div class="abs social" style="left:59px;top:93px"><span style="background:#d9453a"></span><span style="background:#3b5998"></span><span style="background:#1da1f2"></span><span style="background:#0e76a8"></span><span style="background:#cc2020"></span></div>

  <h3 class="abs fh" style="left:205px;top:22px">CONTACTS US</h3>
  <svg class="abs" style="left:206px;top:48px" width="7" height="9"><path d="M3.5 9L0.5 4a3 3 0 1 1 6 0z" fill="#aaa"/></svg>
  <p class="abs contact" style="left:221px;top:46px;width:130px">Lark Vista Perks, no 48 Harbour Lane, Sunvale Bay</p>
  <svg class="abs" style="left:206px;top:83px" width="7" height="7"><path d="M1 0l2 2-1 1.5 2 2L5.5 4.5 7 6.5 5.5 7C3 7 0 4 0 1.5z" fill="#aaa"/></svg>
  <p class="abs contact" style="left:221px;top:81px">Phone: (555) 014-2290</p>
  <svg class="abs" style="left:206px;top:102px" width="7" height="5"><rect width="7" height="5" fill="#aaa"/></svg>
  <p class="abs contact" style="left:221px;top:99px">info@larkvistaperks.com</p>
  <div class="abs pay" style="left:206px;top:121px"><span></span><span></span><span></span><span></span></div>

  <h3 class="abs fh" style="left:385px;top:21px">Quick Links</h3>
  <p class="abs links" style="left:386px;top:41px">Contact Us<br>Shipping &amp; Returns<br>Privacy Notice<br>Conditions of Use<br>My Account</p>

  <h3 class="abs fh" style="left:486px;top:21px">Sign Up For Newsletter</h3>
  <p class="abs links" style="left:486px;top:40px;width:155px;line-height:11px">Excepteur sint occaecat cupidatat non proident, sunt in culpa qui officia deserunt</p>
  <div class="abs field" style="left:486px;top:71px">Enter Name</div>
  <div class="abs field" style="left:486px;top:101px;width:96px">Enter Email</div>
  <div class="abs signup" style="left:582px;top:101px;width:56px;height:24px">SIGNUP</div>
</footer>
<div class="abs rule"></div>
<p class="abs copy">©2017 Lark Vista Perks ., All Rights Reserved.</p>
</body>
</html>
```